Colin Vardek Business card

Hey there, I’m hoping to have a business card designed. I’m in Real estate and just switched to a new Brokerage called: The Harbourline Property Group

The back could just be the company name maybe or whatever looks good!

I’ve attached some logos of our company and some cards my buddy had done up.

On the card:
Colin Vardek
colinvardek@mailora.com
587-412-9065
colinvardek.ca

Target Market(s)

Home buyers and sellers

Industry/Entity Type

Real Estate

Contact Information for Business Card

just looking for a cool and modern design with my picture on it. I like the idea of Black and red being used.

Requirements
Must have
• all the details provided. I'm open to anything. Just want a professional looking card.

```html
<!DOCTYPE html>
<html lang="en">
<head>
<meta charset="utf-8">
<title>Colin Vardek Business Card</title>
<link rel="stylesheet" href="https://fonts.googleapis.com/css2?family=Montserrat:wght@800&family=Poppins:wght@400;500&display=swap">
<style>
  :root {
    --stage: #232325;
    --card: #202024;
    --red: #e0202e;
    --white: #ffffff;
    --muted: #e9e9ec;
  }
  * { margin: 0; padding: 0; box-sizing: border-box; }
  html, body { width: 1200px; height: 711px; overflow: hidden; }
  body {
    background: var(--stage);
    position: relative;
    font-family: "Poppins", sans-serif;
  }
  .card {
    position: absolute;
    top: 90px;
    width: 320px;
    height: 530px;
    background: var(--card);
    border: 2px solid var(--red);
    overflow: hidden;
  }
  .card--back {
    left: 255px;
    border-radius: 160px 0 160px 0;
  }
  .card--front {
    left: 625px;
    border-radius: 0 160px 0 160px;
  }

  /* Back */
  .back-name {
    position: absolute;
    left: 50%;
    top: 50%;
    transform: translate(-50%, -50%) rotate(-90deg);
    font-family: "Montserrat", sans-serif;
    font-weight: 800;
    color: var(--white);
    font-size: 40px;
    line-height: 1.05;
    text-transform: uppercase;
    text-align: center;
    white-space: nowrap;
    letter-spacing: -0.5px;
  }

  /* Front */
  .front-brand {
    position: absolute;
    left: 26px;
    top: 30px;
    font-family: "Montserrat", sans-serif;
    font-weight: 800;
    font-size: 13px;
    line-height: 1.15;
    color: var(--white);
    text-transform: uppercase;
    letter-spacing: 0.2px;
  }
  .portrait {
    position: absolute;
    left: 50%;
    top: 170px;
    transform: translateX(-50%);
    width: 150px;
    height: 150px;
    border-radius: 50%;
    border: 3px solid var(--red);
    background: radial-gradient(circle at 50% 40%, #f2f2f2 0 45%, #d8d8da 70%, #2a2a30 100%);
  }
  .person-name {
    position: absolute;
    left: 0;
    right: 0;
    top: 340px;
    text-align: center;
    font-size: 30px;
    line-height: 1;
  }
  .person-name .first {
    font-family: "Montserrat", sans-serif;
    font-weight: 800;
    color: var(--red);
  }
  .person-name .last {
    font-family: "Poppins", sans-serif;
    font-weight: 400;
    color: var(--white);
  }
  .contact-list {
    position: absolute;
    left: 58px;
    top: 392px;
    list-style: none;
  }
  .contact-list li {
    display: flex;
    align-items: center;
    gap: 10px;
    color: var(--muted);
    font-size: 12.5px;
    line-height: 1;
    margin-bottom: 11px;
  }
  .contact-list svg { width: 14px; height: 14px; flex: none; }
</style>
</head>
<body>

  <section class="card card--back">
    <div class="back-name">The Harbourline<br>Property Group</div>
  </section>

  <section class="card card--front">
    <div class="front-brand">The Harbourline<br>Property Group</div>

    <div class="portrait" role="img" aria-label="Portrait photo of Colin Vardek"></div>

    <h1 class="person-name"><span class="first">Colin</span> <span class="last">Vardek</span></h1>

    <ul class="contact-list">
      <li>
        <svg viewBox="0 0 24 24" aria-hidden="true"><path fill="var(--red)" d="M6.6 10.8a15.1 15.1 0 0 0 6.6 6.6l2.2-2.2a1 1 0 0 1 1-.25 11.4 11.4 0 0 0 3.6.57 1 1 0 0 1 1 1V20a1 1 0 0 1-1 1A17 17 0 0 1 3 4a1 1 0 0 1 1-1h3.5a1 1 0 0 1 1 1c0 1.25.2 2.45.57 3.6a1 1 0 0 1-.25 1z"/></svg>
        587-412-9065
      </li>
      <li>
        <svg viewBox="0 0 24 24" aria-hidden="true"><circle cx="12" cy="12" r="9" fill="none" stroke="var(--red)" stroke-width="2"/><path d="M3 12h18M12 3c3 3 3 15 0 18M12 3c-3 3-3 15 0 18" fill="none" stroke="var(--red)" stroke-width="1.6"/></svg>
        www.colinvardek.ca
      </li>
      <li>
        <svg viewBox="0 0 24 24" aria-hidden="true"><rect x="2" y="5" width="20" height="14" rx="2" fill="var(--red)"/><path d="M3 6l9 7 9-7" fill="none" stroke="var(--card)" stroke-width="1.8"/></svg>
        colinvardek@mailora.com
      </li>
    </ul>
  </section>

</body>
</html>
```